We are a civil construction company that builds bridges, roads, airports and ports. We deliver projects with a large workforce in often sensitive environments.

We a set of visual tools that relate to our minimum 'Environmental Performance Standards'. The images be recognizable and we will use them to educate our work crews.

We are seeking a symbol for each of our Environmental Performance Standards

- Keep all work inside the boundary
- Follow the permit system. (Permit to discharge water, permit to remove vegetation and trees, permit to work in waterways, permit to apply bitumen seal)
- Manage noise and dust at the work location, respect our neighbors
- Approval to work out of hours ( normal working hours are during the day)
- Report all incidents and unexpected finds, an unexpected find is if we find bones or a heritage item while digging
- We must have a plan to manage site water (our works involve disturbing large areas of soil in open environments, we need to manage this to ensure site affected water isn't lost into rivers and creeks)
- Lawfully manage waste. Reduce reuse recycle, clean up as we go
Updates

Hoping to get more designs in, the current design pool is not meeting our desired outcome. If there are more questions or examples we need to provide to assist the designers please let is know

Target Market(s)

Workers on our construction site, visual tools to help educate them on what we need them to do

Colors
86cfc6
33a6d7
f59296
0655a3
fbee3d
1861ab
9bcb3c
add136
cadf82

Requirements
Must have
• A visual symbol for each environmental performance standard

```html
<!DOCTYPE html>
<html lang="en">
<head>
<meta charset="utf-8">
<title>Environmental Performance Standards</title>
<link href="https://fonts.googleapis.com/css2?family=Rubik:wght@800;900&family=Arimo:wght@400&display=swap" rel="stylesheet">
<style>
  :root{
    --sky:#1e9ad0;
    --frame:#1e9ad0;
    --teal:#8ecfc6;
    --rose:#f09497;
    --ocean:#4aa6db;
    --sage:#cce07f;
    --lime:#add136;
    --mist:#e6e7e8;
    --ink:#141414;
    --royal:#1861ab;
    --forest:#1c6b37;
    --moss:#2f6b2a;
    --navy:#1b2c4c;
    --white:#ffffff;
    --signal:#f26b21;
  }
  *{margin:0;padding:0;box-sizing:border-box}
  html,body{width:848px;height:1200px;overflow:hidden;background:var(--white)}
  .canvas{position:relative;width:848px;height:1200px;background:var(--white);font-family:'Rubik',sans-serif}
  .header{position:absolute;left:0;top:0;width:848px;height:159px;background:var(--sky)}
  .stripes{position:absolute;left:0;width:848px;height:30px;
    background:repeating-linear-gradient(-60deg,var(--sky) 0 22px,var(--white) 22px 34px)}
  .stripes.top{top:0}
  .stripes.bottom{top:129px}
  .title{position:absolute;left:0;top:30px;width:848px;text-align:center;color:var(--white);font-weight:900}
  .title .main{display:block;font-size:55px;line-height:58px;letter-spacing:0.5px;margin-top:2px}
  .title .sub{display:block;font-size:34px;line-height:36px;letter-spacing:-0.3px}
  .frame{position:absolute;left:15px;top:174px;width:817px;height:970px;border:6px solid var(--frame);border-bottom:none}
  .frame-base{position:absolute;top:1138px;height:6px;background:var(--frame)}
  .frame-base.left{left:15px;width:222px}
  .frame-base.right{left:617px;width:215px}
  .panel{position:absolute}
  .panel.boundary{left:39px;top:208px;width:381px;height:186px;background:var(--teal)}
  .panel.hours{left:445px;top:208px;width:363px;height:186px;background:var(--rose)}
  .panel.permit{left:39px;top:418px;width:769px;height:186px;background:var(--ocean)}
  .panel.neighbours{left:39px;top:632px;width:769px;height:186px;background:var(--sage)}
  .panel.incidents{left:40px;top:843px;width:317px;height:186px;background:var(--lime)}
  .panel.water{left:382px;top:843px;width:187px;height:186px;background:var(--teal)}
  .panel.waste{left:594px;top:843px;width:214px;height:186px;background:var(--mist)}
  .heading{position:absolute;font-weight:900;color:var(--ink);font-size:23px;line-height:27px;letter-spacing:-0.3px;text-transform:uppercase}
  .heading .accent{color:var(--royal)}
  .heading .light{color:var(--white)}
  .heading .green{color:var(--forest)}
  .heading.right{text-align:right}
  .heading.center{text-align:center;left:0;width:100%}
  .icon{position:absolute;border-radius:6px}
  .caption{position:absolute;width:160px;text-align:center;font-family:'Arimo',sans-serif;font-size:14.5px;line-height:20px}
  .permit .caption{color:var(--navy)}
  .neighbours .caption{color:var(--moss)}
  .brand{position:absolute;left:255px;top:1116px;height:48px;display:flex;align-items:center;gap:12px}
  .brand .mark{width:42px;height:42px;background:var(--ink)}
  .brand .name{font-family:'Rubik',sans-serif;font-weight:900;font-size:36px;color:var(--sky);letter-spacing:0.5px}
</style>
</head>
<body>
<div class="canvas">
  <header class="header">
    <div class="stripes top"></div>
    <h1 class="title"><span class="main">ENVIRONMENTAL</span><span class="sub">PERFORMANCE STANDARDS</span></h1>
    <div class="stripes bottom"></div>
  </header>

  <div class="frame"></div>
  <div class="frame-base left"></div>
  <div class="frame-base right"></div>

  <section class="panel boundary">
    <h2 class="heading" style="left:48px;top:58px">Keep all<br>work inside<br>the <span class="accent">boundary</span></h2>
    <div class="icon" role="img" aria-label="Site fence with keep out sign" style="left:237px;top:72px;width:131px;height:70px;background:linear-gradient(135deg,#3d6b66,#1f3a37)"></div>
  </section>

  <section class="panel hours">
    <div class="icon" role="img" aria-label="Approved permit document with stamp" style="left:50px;top:46px;width:83px;height:98px;background:linear-gradient(180deg,#f4f4f4,#2e8b3e)"></div>
    <h2 class="heading right" style="right:30px;top:58px">Approval<br>to work<br><span class="accent">out of hours</span></h2>
  </section>

  <section class="panel permit">
    <h2 class="heading" style="left:48px;top:52px">Follow<br>the <span class="light">permit</span><br>system.</h2>
    <div class="icon" role="img" aria-label="Pipe discharging water" style="left:227px;top:49px;width:79px;height:62px;background:linear-gradient(180deg,#2a2a2a,#86cfb5)"></div>
    <div class="icon" role="img" aria-label="Cluster of trees" style="left:364px;top:48px;width:92px;height:63px;background:#111"></div>
    <div class="icon" role="img" aria-label="Winding waterway with rocks" style="left:502px;top:49px;width:104px;height:62px;background:linear-gradient(135deg,#d6efff,#7fb6de)"></div>
    <div class="icon" role="img" aria-label="Worker applying bitumen seal on road" style="left:637px;top:49px;width:115px;height:62px;background:linear-gradient(180deg,#2a3a4a,#111)"></div>
    <p class="caption" style="left:185px;top:121px">Permit to<br>discharge water</p>
    <p class="caption" style="left:328px;top:121px;width:170px">Permit to remove<br>vegetation and trees,</p>
    <p class="caption" style="left:475px;top:121px">Permit to work<br>in waterways</p>
    <p class="caption" style="left:614px;top:121px">Permit to apply<br>bitumen seal</p>
  </section>

  <section class="panel neighbours">
    <div class="icon" role="img" aria-label="Speaker and ear noise symbol" style="left:79px;top:45px;width:67px;height:58px;background:#2f3a2a"></div>
    <div class="icon" role="img" aria-label="Dust cloud" style="left:216px;top:50px;width:115px;height:48px;background:linear-gradient(180deg,#f3f5e3,#4a5240)"></div>
    <div class="icon" role="img" aria-label="Handshake" style="left:376px;top:49px;width:76px;height:39px;background:#2f3a2a"></div>
    <p class="caption" style="left:39px;top:109px">Manage noise at<br>the work site</p>
    <p class="caption" style="left:200px;top:109px">Manage dust at<br>the work site</p>
    <p class="caption" style="left:340px;top:109px">Respect<br>our neighbors</p>
    <h2 class="heading right" style="right:30px;top:52px">Manage <span class="accent">noise</span><br><span class="accent">&amp; dust</span> at the<br>work location.</h2>
  </section>

  <section class="panel incidents">
    <div class="icon" role="img" aria-label="Fossil bones unearthed in soil" style="left:112px;top:18px;width:90px;height:83px;border-radius:50%;background:radial-gradient(circle,#e8d5c4,#a0543a)"></div>
    <h2 class="heading center" style="top:101px;font-size:22px;line-height:28px">Report all incidents<br>and <span class="accent">unexpected</span> finds</h2>
  </section>

  <section class="panel water">
    <div class="icon" role="img" aria-label="Site water management plan" style="left:48px;top:29px;width:91px;height:65px;border-radius:2px;background:linear-gradient(135deg,#cfe4f4,#1861ab)"></div>
    <h2 class="heading center" style="top:101px;font-size:22px;line-height:28px">Manager<br>site <span class="accent">water</span></h2>
  </section>

  <section class="panel waste">
    <div class="icon" role="img" aria-label="Recycling arrows" style="left:77px;top:29px;width:55px;height:58px;border-radius:50%;background:radial-gradient(circle,#e6e7e8 38%,#58b947 40%,#1c6b37)"></div>
    <h2 class="heading center" style="top:101px;font-size:22px;line-height:28px">Lawfully<br>manage <span class="green">waste</span></h2>
  </section>

  <footer class="brand">
    <span class="mark"></span>
    <span class="name">Ridgeline Civil</span>
  </footer>
</div>
</body>
</html>
```